Luxurious Product label and box for all natural skincare product. + 30AUD tip to winner.

What I require.
1.     One product label and one-box design.
2.     I must have a mock-up of the bottle with the attached label and the box.
 
I have supplied the following files for the designers to use.
1.     Brand logo file. (logo.zip)
2.     Slogan file. (slogan.psd)
3.     Slogan script file. (italianno.regular.ttf)
4.     Bottle image file. (60ml_moisturiser_bottle.png)
5.     Icon bar file. (Icon_bar_en.zip)
 
Label and box Design
I am interested in your unique design concepts and colors, so please feel free to be creative.
1.     Brand name: Velia
2.     You can use your own choice of colors in your design. I would prefer two colors (excluding logo and slogan colors), although more colors are acceptable for the right design.
3.     Label and box to have a background color or pattern.
4.     I would like the icon bar to wrap around the bottom of the label and box, covering the full width of all sides of the box.
5.     The height of the icon bar should be about 7mm to 10mm high.   
6.     The hex code for the icon bar color is #EDD6D4. The color of the icons can be any color the designer chooses.
7.     The positioning of the icons are as follows.
a)     The front panel has three icons. From left to right, they are; 100% Vegan, Product of Australia, and 100% Natural.
b)     The left side panel has three icons. From the front of the label/box to the back of the label/box, they are; Cruelty-Free, Ethical & Sustainable, and Please Recycle.
c)     The right side panel has only one icon situated at the front of the right side of the label/box. The icon is 6 Months Once Open.
 
Label.
1.     The label will be a three-panel label.
2.     The label will contain text in all three panels; however, only the text for the front panel of the label is supplied in this brief. For now, use Lorem Ipsum placeholder text to fill spaces.
3.     The final text will be provided to the winning designer so they can apply the text to the left and right panels of the label.
4.     Label size. Width 104mm x Height 83mm.
5.     The final design file must include bleed and cut lines.
 
Box.
1.     The box will contain text on all four sides; however, only the text for the front of the box is supplied in this brief. For now, use Lorem Ipsum placeholder text to fill spaces.
2.     The final text will be provided to the winning designer so they can apply the text to the left and right sides and the back of the box.
3.     The box size is 40mm wide x 40mm deep x 140mm high.
4.     The final design file must include bleed and cut lines.
 
Front Panel wording.
1.     Logo.
2.     Slogan.
3.     Moisturiser.
4.     Hydrate & Nourish.
5.     Hyaluronic Acid, Desert Lime & Green Tea.
6.     All Skin Types - Dry – Dehydrated.
7.     Icon bar.
8.     60mL
 
Bottle size
60ml White Bottle – 13.5cm High x 3.5cm Wide.

Target Market(s)

Beauty-minded Asian consumers between the age of 32 and 75 who take a proactive approach in maintaining younger-looking skin. Those who already know the danger of damaged skin caused by skincare containing harsh chemicals, and therefore choose effective natural/organic solutions to meet their skincare needs. Those who wish a more radiant glow and youthful appearance to their skin. Usually, a two-income middle to high-income bracket couple with a mindset for health and beauty.

Industry/Entity Type

Beauty and skincare.

Font styles to use
Other font styles liked:
• Logo and slogan script supplied. Designer to choose all other font or script.

Colors

Designer to choose colors to be used in the design.

Requirements
Must have
• A mock-up label on the bottle and a mock-up box. My logo and slogan are already designed with my chosen font and color.
Nice to have
• I like soft pastel colors with perhaps a small amount of stronger color.

```html
<!DOCTYPE html>
<html lang="en">
<head>
<meta charset="utf-8">
<title>Velia Skincare – Moisturiser box and label</title>
<link href="https://fonts.googleapis.com/css2?family=Montserrat:wght@400;500;700&family=Oswald:wght@500;600&family=Roboto+Condensed:wght@400;700&display=swap" rel="stylesheet">
<style>
:root{
  --page:#ffffff;
  --panel:#141312;
  --pattern-a:#1b1813;
  --pattern-b:#262017;
  --ornament-a:rgba(120,92,40,.22);
  --ornament-b:rgba(40,32,18,.05);
  --gold:#d9b350;
  --gold-light:#f3d67a;
  --gold-dark:#b88a2c;
  --green:#4f9a2c;
  --white:#ffffff;
  --text:#e9e6e0;
  --badge:#edd6d4;
  --badge-ink:#3a2a2a;
  --rule:#cfcfcf;
}
*{margin:0;padding:0;box-sizing:border-box}
html,body{width:769px;height:1200px;overflow:hidden;background:var(--page)}
.canvas{position:relative;width:769px;height:1200px}
.panel{position:absolute;background:var(--panel);overflow:hidden;color:var(--white);font-family:'Montserrat',sans-serif}
.leaf-pattern{position:absolute;inset:0;background:linear-gradient(135deg,var(--panel) 0%,var(--pattern-b) 30%,var(--pattern-a) 55%,var(--pattern-b) 80%,var(--panel) 100%)}
.ornament-area{position:absolute;background:linear-gradient(180deg,var(--ornament-b),var(--ornament-a) 50%,var(--ornament-b))}
.abs{position:absolute;text-align:center}
.brand-name{font-family:'Montserrat',sans-serif;font-weight:500;color:var(--gold)}
.brand-dot{display:inline-block;border-radius:50%;background:var(--gold);vertical-align:middle}
.slogan{font-family:'Montserrat',sans-serif;font-weight:400;color:var(--green)}
.product-name{font-family:'Oswald',sans-serif;font-weight:600;background:linear-gradient(180deg,var(--gold-light),var(--gold-dark));-webkit-background-clip:text;background-clip:text;-webkit-text-fill-color:transparent;letter-spacing:-.5px}
.claim{font-weight:400;color:var(--white);line-height:1.18}
.skin-band{position:absolute;left:0;right:0;background:linear-gradient(90deg,var(--gold-dark),var(--gold-light) 50%,var(--gold-dark));color:#1b1710;font-weight:700;text-align:center;line-height:1.25}
.ingredients{font-family:'Oswald',sans-serif;font-weight:500;color:var(--white);white-space:nowrap}
.ingredients .sep{margin:0 4px}
.badge{position:absolute;border-radius:50%;background:var(--badge);color:var(--badge-ink);display:flex;flex-direction:column;align-items:center;justify-content:center;font-weight:700;text-align:center;line-height:1.05}
.badge svg{display:block;margin-bottom:2px}
.volume{position:absolute;display:flex;align-items:center;gap:6px;color:var(--white);font-weight:400}
.volume .line{height:1px;background:var(--rule);flex:1}
.copy{position:absolute;color:var(--text);font-size:6.2px;line-height:8.1px;text-align:justify}
.copy p{margin-bottom:8px}
.copy h3{font-weight:400;font-size:11px;margin:6px 0 8px}
.copy ul{list-style:none}
.copy li{display:flex;align-items:center;gap:4px;margin-bottom:4px}
.facts{position:absolute;background:#fff;color:#111;font-family:'Roboto Condensed',sans-serif;padding:3px;border:1.5px solid #111}
.facts h4{font-size:13px;font-weight:700;line-height:1.05}
.facts .serving{font-size:7.8px;line-height:7.6px;border-bottom:4px solid #111;padding-bottom:2px}
.facts table{width:100%;border-collapse:collapse;font-size:5.3px;line-height:6.6px}
.facts th{font-weight:400;text-align:right;border-bottom:2px solid #111;padding:2px 0}
.facts td.num{text-align:right}
.facts .note{font-size:4.6px;line-height:6px;border-top:2px solid #111;border-bottom:1px solid #111;padding:2px 0}
.facts .other{font-size:5.2px;line-height:7px;padding-top:2px}
</style>
</head>
<body>
<div class="canvas">

  <section class="panel box-front" style="left:44px;top:296px;width:173px;height:604px">
    <div class="leaf-pattern" role="img" aria-label="Dark background with faint gold leaf line pattern"></div>
    <div class="ornament-area" role="img" aria-label="Gold light swirl ornament framing the product name" style="left:0;right:0;top:154px;height:205px"></div>

    <div class="abs" style="left:0;right:0;top:88px">
      <span class="brand-name" style="font-size:17px"><span class="brand-dot" style="width:7px;height:7px;margin-right:5px"></span>Velia Skincare</span>
    </div>
    <div class="abs slogan" style="left:0;right:0;top:117px;font-size:12px">grown by nature</div>

    <div class="abs product-name" style="left:0;right:0;top:203px;font-size:31px;line-height:38px">MOISTURISER</div>
    <div class="abs claim" style="left:0;right:0;top:244px;font-size:26px">Hydrate &amp;<br>Nourish</div>

    <div class="skin-band" style="top:382px;height:63px;font-size:17.5px;padding-top:9px">All Skin Types<br>Dry – Dehydrated</div>

    <div class="abs ingredients" style="left:0;right:0;top:467px;font-size:8.8px">Hyaluronic Acid<span class="sep">|</span>Desert Lime<span class="sep">|</span>Green Tea</div>

    <div class="badge" style="left:12px;top:506px;width:46px;height:46px;font-size:4.8px">
      <svg width="15" height="14" viewBox="0 0 24 22"><path d="M12 21 C4 14 1 10 1 6 A5 5 0 0 1 12 4 A5 5 0 0 1 23 6 C23 10 20 14 12 21Z" fill="none" stroke="#3a2a2a" stroke-width="1.8"/></svg>100%<br>Vegan</div>
    <div class="badge" style="left:64px;top:506px;width:46px;height:46px;font-size:4.6px">Product of<br>Australia</div>
    <div class="badge" style="left:116px;top:506px;width:46px;height:46px;font-size:4.8px">
      <svg width="16" height="12" viewBox="0 0 24 18"><path d="M12 17 C8 13 8 6 12 1 C16 6 16 13 12 17Z M12 17 C6 17 2 13 1 7 C6 8 10 12 12 17Z M12 17 C18 17 22 13 23 7 C18 8 14 12 12 17Z" fill="none" stroke="#3a2a2a" stroke-width="1.5"/></svg>100%<br>Natural</div>

    <div class="volume" style="left:6px;right:6px;top:571px;font-size:12px"><span class="line"></span>60mL<span class="line"></span></div>
  </section>

  <section class="panel bottle-label" style="left:252px;top:384px;width:474px;height:378px">
    <div class="leaf-pattern" role="img" aria-label="Dark background with faint gold leaf line pattern"></div>
    <div class="ornament-area" role="img" aria-label="Gold light swirl ornament framing the product name" style="left:160px;width:155px;top:115px;height:170px"></div>

    <div class="copy" style="left:10px;top:46px;width:137px">
      <p>Lorem Ipsum is simply dummy text of the printing and typesetting industry. Lorem Ipsum has been the industry's standard dummy text ever since the 1500s, when an unknown printer took a galley of type and scrambled it to make a type specimen book. It has survived not only five centuries, but also the leap into electronic typesetting, remaining essentially unchanged.</p>
      <p>Lorem Ipsum is simply dummy text of the printing and typesetting industry. Lorem Ipsum has been the industry's standard dummy text ever since the 1500s, when an unknown printer took a galley of type and scrambled it to make a type specimen book. It has survived not only five centuries, but also the leap into electronic typesetting, remaining essentially unchanged.</p>
      <p style="text-align:left">The standard chunk of Lorem Ipsum<br>used since the 1500s is reproduced below<br>for those interested.</p>
      <h3>Why do we use it?</h3>
      <ul>
        <li><svg width="7" height="6" viewBox="0 0 10 8"><path d="M1 4 L4 7 L9 1" fill="none" stroke="#fff" stroke-width="1.6"/></svg>The standard chunk of Lorem Ipsum</li>
        <li><svg width="7" height="6" viewBox="0 0 10 8"><path d="M1 4 L4 7 L9 1" fill="none" stroke="#fff" stroke-width="1.6"/></svg>The point of using Lorem Ipsum</li>
      </ul>
    </div>
    <div class="badge" style="left:11px;top:312px;width:42px;height:42px;font-size:4.4px">Cruelty<br>Free</div>
    <div class="badge" style="left:58px;top:312px;width:42px;height:42px;font-size:3.9px">Ethical&amp;<br>Sustainable</div>
    <div class="badge" style="left:106px;top:312px;width:42px;height:42px;font-size:4.4px">
      <svg width="14" height="13" viewBox="0 0 24 22"><path d="M12 2 L17 10 M19 14 L22 19 H14 M8 19 H2 L6 12 M9 7 L12 2" fill="none" stroke="#3a2a2a" stroke-width="1.8"/></svg>Please<br>Recycle</div>

    <div class="abs" style="left:160px;width:155px;top:68px">
      <span class="brand-name" style="font-size:15.5px"><span class="brand-dot" style="width:6px;height:6px;margin-right:4px"></span>Velia Skincare</span>
    </div>
    <div class="abs slogan" style="left:160px;width:155px;top:93px;font-size:10.5px">grown by nature</div>
    <div class="abs product-name" style="left:160px;width:155px;top:153px;font-size:26px;line-height:32px">MOISTURISER</div>
    <div class="abs claim" style="left:160px;width:155px;top:186px;font-size:16.5px">Hydrate &amp;<br>Nourish</div>
    <div class="abs ingredients" style="left:160px;width:155px;top:228px;font-size:7.6px">All Skin Types - Dry - Dehydrated</div>
    <div class="abs ingredients" style="left:160px;width:155px;top:283px;font-size:8.2px">Hyaluronic Acid<span class="sep">|</span>Desert Lime<span class="sep">|</span>Green Tea</div>
    <div class="badge" style="left:168px;top:312px;width:42px;height:42px;font-size:4.4px">
      <svg width="13" height="12" viewBox="0 0 24 22"><path d="M12 21 C4 14 1 10 1 6 A5 5 0 0 1 12 4 A5 5 0 0 1 23 6 C23 10 20 14 12 21Z" fill="none" stroke="#3a2a2a" stroke-width="1.8"/></svg>100%<br>Vegan</div>
    <div class="badge" style="left:216px;top:312px;width:42px;height:42px;font-size:4.1px">Product of<br>Australia</div>
    <div class="badge" style="left:264px;top:312px;width:42px;height:42px;font-size:4.4px">
      <svg width="14" height="11" viewBox="0 0 24 18"><path d="M12 17 C8 13 8 6 12 1 C16 6 16 13 12 17Z M12 17 C6 17 2 13 1 7 C6 8 10 12 12 17Z M12 17 C18 17 22 13 23 7 C18 8 14 12 12 17Z" fill="none" stroke="#3a2a2a" stroke-width="1.5"/></svg>100%<br>Natural</div>
    <div class="volume" style="left:172px;width:130px;top:359px;font-size:10px"><span class="line"></span>60mL<span class="line"></span></div>

    <div class="facts" style="left:324px;top:51px;width:145px;height:167px">
      <h4>Supplement Facts</h4>
      <div class="serving">Serving Size: 1 Capsule<br>Servings Per Container: 60</div>
      <table>
        <tr><th colspan="2">Amount Per Serving</th><th>% DV*</th></tr>
        <tr><td>Phosphatidylserine</td><td class="num">150 mg</td><td class="num">†</td></tr>
        <tr><td>Acetyl L-Carnitine</td><td class="num">100 mg</td><td class="num">†</td></tr>
        <tr><td>Alpha Lipoic Acid R Form</td><td class="num">60 mg</td><td class="num">†</td></tr>
        <tr><td>Resveratrol</td><td class="num">60 mg</td><td class="num">†</td></tr>
        <tr><td>Ascorbic Acid</td><td class="num">50 mg</td><td class="num">85%</td></tr>
        <tr><td>Green Tea Extract</td><td class="num">25 mg</td><td class="num">†</td></tr>
        <tr><td>Vinpocetine</td><td class="num">10 mg</td><td class="num">†</td></tr>
        <tr><td>Vitamin B-6</td><td class="num">5 mg</td><td class="num">250%</td></tr>
        <tr><td>Folic Acid</td><td class="num">300 mcg</td><td class="num">80%</td></tr>
        <tr><td>Biotin</td><td class="num">400 mcg</td><td class="num">130%</td></tr>
        <tr><td>Vitamin B-12</td><td class="num">25 mcg</td><td class="num">420%</td></tr>
      </table>
      <div class="note">*Percent daily values based on a 2000 calories diet.<br>†Daily Value not established.</div>
      <div class="other">Other Ingredients: Magnesium Stearate, Silicon Dioxide and Cellulose (vegetable capsule).</div>
    </div>
    <div class="copy" style="left:324px;top:232px;width:145px">
      <p>Lorem Ipsum is simply dummy text of the printing and typesetting industry. Lorem Ipsum has been the industry's standard dummy text ever since the 1500s, when an unknown printer took a galley of type and scrambled it to make a type specimen book. It has survived not only five centuries, but also the leap into electronic typesetting, remaining essentially unchanged. It was</p>
    </div>
    <div class="badge" style="left:328px;top:312px;width:42px;height:42px;font-size:4.2px">
      <svg width="13" height="11" viewBox="0 0 24 20"><rect x="3" y="6" width="18" height="13" rx="2" fill="none" stroke="#3a2a2a" stroke-width="1.5"/><path d="M4 4 L20 1" stroke="#3a2a2a" stroke-width="1.5"/><text x="12" y="16" font-size="7" text-anchor="middle" fill="#3a2a2a" font-family="Montserrat,sans-serif">6M</text></svg>6Months<br>OnceOpen</div>
  </section>

</div>
</body>
</html>
```